Natural Medicine & Health/Fitness Coaching studio requires web page

Require a innovative web page for a studio that coaches clients to better health, nutrition and fitness. The studio compromises of Clinical Nutritionists, Naturopaths, Rehab Trainers, Personal Trainers and Sport Coaches. Would like to see earthy but bold designs emphasizing nutritional health and athletic performance.
Updates

Design only launched today.

Target Market(s)

All genders from 20's to 60's, as well as families

Industry/Entity Type

Nutritionist

Coding

Coded - Design and coding required

Number of Pages Required

3 page

Colors
abd037
3277b5
fbee3d
fece3e
33b8a4
f04a50

Requirements
Must have
• Online booking system, ability to message
• Home page
• Coaching/Fitness page
• Nutritional Medicine page
• Must be suitable for both Fitness and Nutrition

```html
<!DOCTYPE html>
<html lang="en">
<head>
<meta charset="utf-8">
<title>Verdant Vigor Nutritional Therapy</title>
<link href="https://fonts.googleapis.com/css2?family=Poppins:wght@400;500;600;700&family=Open+Sans:wght@400;600&display=swap" rel="stylesheet">
<style>
:root{
  --teal:#33b8a4;
  --teal-dark:#1f9a86;
  --green:#abd037;
  --blue:#3277b5;
  --yellow:#fbee3d;
  --red:#f04a50;
  --ink:#1d1d1d;
  --text:#555;
  --ghost:#ececec;
  --light:#f4f4f2;
  --white:#fff;
}
*{margin:0;padding:0;box-sizing:border-box}
html,body{width:1200px;height:4675px;overflow:hidden}
body{font-family:"Open Sans",Arial,sans-serif;color:var(--text);background:var(--white);position:relative}
.abs{position:absolute}
h1,h2,h3,h4{font-family:"Poppins",Arial,sans-serif;font-weight:600;color:var(--ink)}

/* top bar */
.topbar{top:0;left:0;width:1200px;height:34px;background:var(--teal);color:#fff;font-size:13px}
.topbar .contact{left:108px;top:8px;display:flex;gap:22px}
.topbar .social{right:90px;top:8px;display:flex;gap:8px}
.topbar .social span{width:18px;height:18px;background:#fff;border-radius:3px;opacity:.9}

/* header */
.header{top:34px;left:0;width:1200px;height:122px;background:#fff}
.brand{left:94px;top:40px;display:flex;align-items:center;gap:10px;font-family:"Poppins",sans-serif;font-weight:600;font-size:30px;color:var(--teal-dark);line-height:34px}
.brand .dot{width:22px;height:22px;border-radius:50%;background:var(--green)}
.brand small{display:block;font-size:12px;font-weight:600;color:var(--teal-dark);letter-spacing:1px;line-height:16px}
.nav{right:90px;top:52px;display:flex;gap:38px;font-family:"Poppins",sans-serif;font-size:16px;color:var(--ink);align-items:center}
.nav .active{color:var(--teal)}

/* hero */
.hero{top:156px;left:0;width:1200px;height:624px;overflow:hidden;
  background:linear-gradient(180deg,#eef1f3 0%,#e3e6e6 55%,#d6d0c6 100%)}
.hero .photo{left:420px;top:0;width:780px;height:624px;
  background:
    radial-gradient(ellipse 260px 330px at 68% 48%,rgba(120,92,70,.55),rgba(120,92,70,0) 70%),
    linear-gradient(180deg,#d9e3ea 0%,#bfcfdb 38%,#9fb4c2 46%,#cfc6b8 60%,#b8ab98 100%);
  -webkit-mask-image:linear-gradient(90deg,transparent 0,#000 28%);
          mask-image:linear-gradient(90deg,transparent 0,#000 28%)}
.hero h1{left:88px;top:70px;font-size:84px;line-height:92px;font-weight:700;color:var(--teal-dark)}
.hero .sub{left:90px;top:258px;font-family:"Poppins",sans-serif;font-weight:600;font-size:24px;color:var(--ink)}
.hero .dots{right:22px;top:240px;display:flex;flex-direction:column;gap:14px}
.hero .dots span{width:8px;height:8px;border-radius:50%;background:#fff}
.hero .dots span.on{background:var(--red)}

/* section titles */
.ghost{font-family:"Poppins",sans-serif;font-weight:500;font-size:100px;color:var(--ghost);white-space:nowrap;line-height:1}
.sec-title{font-size:44px;text-align:center;width:1200px;left:0}
.sec-sub{font-size:20px;color:var(--ink);text-align:center;width:1200px;left:0}

/* services */
.service{width:300px;text-align:center}
.service .icon{width:104px;height:104px;margin:0 auto;border-radius:50%;background:#eef6d8;border:3px solid var(--teal);position:relative}
.service .icon::after{content:"";position:absolute;left:26px;top:26px;width:46px;height:46px;border-radius:50%;background:var(--green)}
.service h3{font-size:24px;font-weight:500;margin:22px 0 10px}
.service p{font-size:13px;line-height:20px}
.service .chev{margin-top:20px}

/* about */
.about{top:1450px;left:0;width:1200px;height:595px;background:var(--light);overflow:hidden}
.about .photo{left:0;top:0;width:600px;height:595px;
  background:
    radial-gradient(ellipse 150px 200px at 58% 45%,rgba(201,76,112,.55),rgba(201,76,112,0) 70%),
    radial-gradient(ellipse 180px 160px at 12% 30%,rgba(70,80,140,.35),rgba(70,80,140,0) 70%),
    radial-gradient(ellipse 160px 170px at 10% 78%,rgba(200,70,60,.35),rgba(200,70,60,0) 70%),
    linear-gradient(120deg,#f6f2ea,#eee3d8 55%,#f2efea)}
.about h2{left:620px;top:100px;font-size:46px}
.about p{left:620px;top:170px;width:490px;font-size:14px;line-height:28px;color:#444;text-align:justify}
.btn-outline{left:620px;top:390px;width:150px;height:40px;border:1.5px solid var(--red);border-radius:20px;color:var(--red);font-size:14px;display:flex;align-items:center;justify-content:center}

/* training */
.card{top:2353px;width:318px;height:415px;background:#fff;box-shadow:0 2px 10px rgba(0,0,0,.18);text-align:center}
.card .photo{width:318px;height:222px}
.card h4{font-size:19px;margin:30px 0 12px}
.card p{font-size:13px;line-height:22px;padding:0 30px}
.btn-pill{display:inline-block;margin-top:14px;width:110px;height:30px;line-height:30px;border-radius:15px;background:var(--teal-dark);color:#fff;font-size:13px}

/* testimonial */
.testi{top:2920px;left:0;width:1200px;height:620px;background:linear-gradient(180deg,#262626,#141414);overflow:hidden}
.testi .ghost{color:rgba(255,255,255,.08)}
.quote{top:212px;width:490px;height:218px;background:#fff;border-radius:4px}
.quote .avatar{left:-20px;top:50px;width:124px;height:124px;border-radius:50%;background:linear-gradient(135deg,#d8b99c,#7a5a45);border:5px solid #fff}
.quote h4{left:150px;top:30px;font-size:17px;font-weight:500}
.quote p{left:150px;top:62px;width:300px;font-size:14px;line-height:22px}
.quote .name{right:40px;top:160px;font-size:17px;color:var(--ink)}
.quote svg{position:absolute;right:36px;top:24px}

/* booking */
.booking h2{left:90px;top:3692px;font-size:48px;font-weight:500}
.booking .sub{left:90px;top:3760px;font-size:20px;color:var(--ink)}
.field{height:44px;background:#f0f0f0;border:1px solid #c9c9c9;font-size:13px;color:#333;padding:12px 10px}
.submit{left:94px;top:4093px;width:120px;height:38px;border-radius:19px;background:var(--teal-dark);color:#fff;font-family:"Poppins",sans-serif;font-weight:600;font-size:17px;display:flex;align-items:center;justify-content:center}
.booking .photo{left:690px;top:3580px;width:460px;height:720px;
  background:
    radial-gradient(ellipse 110px 130px at 55% 22%,rgba(150,110,85,.75),rgba(150,110,85,0) 70%),
    radial-gradient(ellipse 150px 340px at 50% 60%,rgba(176,132,104,.65),rgba(176,132,104,0) 70%),
    radial-gradient(ellipse 60px 60px at 30% 92%,rgba(240,74,80,.45),rgba(240,74,80,0) 70%)}

/* footer */
.footer{top:4270px;left:0;width:1200px;height:405px;background:#0f0f0f;color:#ccc;font-size:13px}
.footer h4{font-family:"Poppins",sans-serif;color:#fff;font-size:14px;font-weight:500;margin-bottom:22px;letter-spacing:.5px}
.footer ul{list-style:none;line-height:22px}
.footer li::before{content:"› ";color:#fff}
.footer .row{display:flex;gap:8px;align-items:flex-start;margin-bottom:12px;line-height:18px}
.mail{width:216px;height:40px;border:1.5px solid #fff;border-radius:20px;display:flex;align-items:center;justify-content:space-between;padding:0 12px 0 22px;margin-top:14px;color:#999}
.copy{left:0;width:1200px;top:358px;text-align:center;color:#ccc;font-size:13px}
</style>
</head>
<body>

<div class="abs topbar">
  <div class="abs contact"><span>☎ (555) 010 2846</span><span>✉ hello@verdantvigor.test</span></div>
  <div class="abs social"><span></span><span></span><span></span><span></span></div>
</div>

<header class="abs header">
  <div class="abs brand"><span class="dot"></span><div>Verdant Vigor<small>Nutritional Therapy</small></div></div>
  <nav class="abs nav">
    <span class="active">Home</span><span>About us</span><span>Coaching</span><span>Fitness</span><span>Nutrition</span><span>Contact us</span>
    <svg width="22" height="22" viewBox="0 0 22 22"><circle cx="9" cy="9" r="7" fill="none" stroke="#1d1d1d" stroke-width="2.6"/><line x1="14" y1="14" x2="20" y2="20" stroke="#1d1d1d" stroke-width="3" stroke-linecap="round"/></svg>
  </nav>
</header>

<section class="abs hero">
  <div class="abs photo" role="img" aria-label="Athlete in sportswear crouching in a starting position by the sea"></div>
  <h1 class="abs">Verdant Vigor<br>Nutritional</h1>
  <div class="abs sub">Neque porro quisquam est qui dolorem</div>
  <div class="abs dots"><span></span><span></span><span class="on"></span><span></span></div>
  <svg class="abs" style="left:0;top:480px" width="1200" height="144" viewBox="0 0 1200 144" preserveAspectRatio="none">
    <defs><linearGradient id="heroBand" x1="0" x2="1"><stop offset="0" stop-color="#1fa58f"/><stop offset="1" stop-color="#abd037"/></linearGradient></defs>
    <polygon points="0,80 1200,0 1200,50 0,144" fill="url(#heroBand)"/>
    <polygon points="0,144 1200,60 1200,144" fill="#fff"/>
  </svg>
</section>

<section>
  <div class="abs ghost" style="left:330px;top:820px">Our Services</div>
  <h2 class="abs sec-title" style="top:862px">Our Services</h2>
  <div class="abs sec-sub" style="top:918px">Neque porro quisquam est qui dolorem</div>
  <svg class="abs" style="left:150px;top:1140px" width="900" height="20" viewBox="0 0 900 20">
    <g stroke="#fbee3d" stroke-width="3" fill="none">
      <line x1="130" y1="10" x2="350" y2="10"/><polyline points="340,3 350,10 340,17"/>
      <line x1="500" y1="10" x2="700" y2="10"/><polyline points="690,3 700,10 690,17"/>
    </g>
  </svg>
  <div class="abs service" style="left:71px;top:1050px">
    <div class="icon" role="img" aria-label="Coaching icon: coach with a stopwatch"></div>
    <h3>Coaching</h3>
    <p>Lorem Ipsum has been the industry's<br>standard dummy text ever since the<br>1500s, when an unknown</p>
    <div class="chev"><svg width="20" height="20" viewBox="0 0 20 20"><polyline points="4,3 10,9 16,3" fill="none" stroke="#222" stroke-width="2.4"/><polyline points="4,10 10,16 16,10" fill="none" stroke="#222" stroke-width="2.4"/></svg></div>
  </div>
  <div class="abs service" style="left:424px;top:1050px">
    <div class="icon" role="img" aria-label="Fitness icon: exercise bike"></div>
    <h3>Fitness</h3>
    <p>Lorem Ipsum has been the industry's<br>standard dummy text ever since the<br>1500s, when an unknown</p>
    <div class="chev"><svg width="20" height="20" viewBox="0 0 20 20"><polyline points="4,3 10,9 16,3" fill="none" stroke="#222" stroke-width="2.4"/><polyline points="4,10 10,16 16,10" fill="none" stroke="#222" stroke-width="2.4"/></svg></div>
  </div>
  <div class="abs service" style="left:773px;top:1050px">
    <div class="icon" role="img" aria-label="Nutrition icon: scale with a measuring tape"></div>
    <h3>Nutrition</h3>
    <p>Lorem Ipsum has been the industry's<br>standard dummy text ever since the<br>1500s, when an unknown</p>
    <div class="chev"><svg width="20" height="20" viewBox="0 0 20 20"><polyline points="4,3 10,9 16,3" fill="none" stroke="#222" stroke-width="2.4"/><polyline points="4,10 10,16 16,10" fill="none" stroke="#222" stroke-width="2.4"/></svg></div>
  </div>
</section>

<section class="abs about">
  <div class="abs photo" role="img" aria-label="Smiling woman lifting a small dumbbell beside bowls of berries and nuts"></div>
  <div class="abs ghost" style="left:760px;top:40px;color:#e6e6e4">About us</div>
  <h2 class="abs">About us</h2>
  <p class="abs">It is a long established fact that a reader will be distracted by the readable content of a page when looking at its layout. The point of using Lorem Ipsum is that it has a more-or-less normal distribution of letters, as opposed to using 'Content here, content here', making it look like readable English. Many desktop publishing packages and web page editors now use Lorem Ipsum as their default model text, and a search for 'lorem ipsum' will uncover many web sites still in their infancy.</p>
  <div class="abs btn-outline">Read More »</div>
  <svg class="abs" style="left:0;top:480px" width="1200" height="115" viewBox="0 0 1200 115" preserveAspectRatio="none">
    <polygon points="500,115 1200,20 1200,115" fill="#abd037"/>
    <polygon points="0,115 1200,70 1200,115" fill="#fff"/>
  </svg>
</section>

<section>
  <div class="abs ghost" style="left:330px;top:2150px">Our Training</div>
  <h2 class="abs sec-title" style="top:2200px">Our Training</h2>
  <div class="abs sec-sub" style="top:2262px">Neque porro quisquam est qui dolorem</div>
  <div class="abs card" style="left:94px">
    <div class="photo" role="img" aria-label="Group fitness class stretching in a studio" style="background:linear-gradient(135deg,#9fc6dd,#5e86a6)"></div>
    <h4>Neque porro quisquam</h4>
    <p>It is a long established fact that a reader will be distracted by the readable content of a page when looking at its layout.</p>
    <span class="btn-pill">View More</span>
  </div>
  <div class="abs card" style="left:437px">
    <div class="photo" role="img" aria-label="Women holding dumbbells in a gym class" style="background:linear-gradient(135deg,#e7c5c9,#a98487)"></div>
    <h4>Dolorem ipsum quia</h4>
    <p>It is a long established fact that a reader will be distracted by the readable content of a page when looking at its layout.</p>
    <span class="btn-pill">View More</span>
  </div>
  <div class="abs card" style="left:786px">
    <div class="photo" role="img" aria-label="People doing lunges outdoors on grass" style="background:linear-gradient(135deg,#a5cf77,#4f8a3a)"></div>
    <h4>Neque porro quisquam</h4>
    <p>It is a long established fact that a reader will be distracted by the readable content of a page when looking at its layout.</p>
    <span class="btn-pill">View More</span>
  </div>
</section>

<section class="abs testi">
  <div class="abs" role="img" aria-label="Dumbbells, sneakers and a skipping rope on a dark floor" style="left:0;top:0;width:460px;height:500px;background:radial-gradient(ellipse 120px 90px at 12% 28%,rgba(254,206,62,.55),rgba(254,206,62,0) 70%),radial-gradient(ellipse 130px 110px at 55% 12%,rgba(200,200,200,.35),rgba(200,200,200,0) 70%),radial-gradient(ellipse 200px 60px at 40% 88%,rgba(50,119,181,.45),rgba(50,119,181,0) 70%),radial-gradient(ellipse 80px 120px at 4% 70%,rgba(171,208,55,.35),rgba(171,208,55,0) 70%)"></div>
  <div class="abs ghost" style="left:440px;top:60px">Testimonial</div>
  <h2 class="abs" style="left:0;width:1200px;text-align:center;top:90px;font-size:46px;color:#fff;font-weight:500">Testimonial</h2>
  <div class="abs quote" style="left:94px">
    <div class="abs avatar" role="img" aria-label="Portrait of a client"></div>
    <svg width="48" height="36" viewBox="0 0 48 36"><path d="M2 36V20C2 8 8 2 18 0v7c-5 2-7 6-7 11h7v18zM28 36V20C28 8 34 2 44 0v7c-5 2-7 6-7 11h7v18z" fill="#f04a50"/></svg>
    <h4 class="abs">Neque porro quisqum</h4>
    <p class="abs">The point of using Lorem Ipsum is that it has a more-or-less normal distribution of letters, as opposed to using 'Content</p>
    <div class="abs name">- &nbsp;&nbsp;Mara</div>
  </div>
  <div class="abs quote" style="left:616px">
    <div class="abs avatar" role="img" aria-label="Portrait of a client"></div>
    <svg width="48" height="36" viewBox="0 0 48 36"><path d="M2 36V20C2 8 8 2 18 0v7c-5 2-7 6-7 11h7v18zM28 36V20C28 8 34 2 44 0v7c-5 2-7 6-7 11h7v18z" fill="#f04a50"/></svg>
    <h4 class="abs">Dolorem ipsum quia dolor</h4>
    <p class="abs">The point of using Lorem Ipsum is that it has a more-or-less normal distribution of letters, as opposed to using 'Content</p>
    <div class="abs name">- Jonah</div>
  </div>
  <svg class="abs" style="left:0;top:490px" width="1200" height="130" viewBox="0 0 1200 130" preserveAspectRatio="none">
    <defs><linearGradient id="testiBand" x1="0" x2="1"><stop offset="0" stop-color="#abd037"/><stop offset="1" stop-color="#1fa58f"/></linearGradient></defs>
    <polygon points="0,0 1200,60 1200,130 0,130" fill="url(#testiBand)"/>
    <polygon points="0,130 0,70 1200,100 1200,130" fill="#fff"/>
  </svg>
</section>

<section class="booking">
  <div class="abs ghost" style="left:300px;top:3660px">Online Booking</div>
  <div class="abs photo" role="img" aria-label="Athletic woman in sportswear mid-stride"></div>
  <h2 class="abs">Online Booking</h2>
  <div class="abs sub">Neque porro quisquam est qui dolorem</div>
  <div class="abs field" style="left:94px;top:3826px;width:286px">Name</div>
  <div class="abs field" style="left:400px;top:3826px;width:286px">Phone</div>
  <div class="abs field" style="left:94px;top:3884px;width:286px">Email</div>
  <div class="abs field" style="left:400px;top:3884px;width:286px">Address</div>
  <div class="abs field" style="left:94px;top:3946px;width:592px;height:116px">Message</div>
  <div class="abs submit">Submit</div>
</section>

<footer class="abs footer">
  <svg class="abs" style="left:0;top:-90px" width="1200" height="140" viewBox="0 0 1200 140" preserveAspectRatio="none">
    <defs><linearGradient id="footBand" x1="0" x2="1"><stop offset="0" stop-color="#1fa58f"/><stop offset="1" stop-color="#abd037"/></linearGradient></defs>
    <polygon points="0,50 1200,0 1200,70 0,90" fill="url(#footBand)"/>
    <polygon points="0,90 1200,40 1200,140 0,140" fill="#0f0f0f"/>
  </svg>
  <div class="abs" style="left:112px;top:150px">
    <h4>LINKS</h4>
    <ul><li>Home</li><li>About</li><li>Blog</li><li>Contact</li></ul>
  </div>
  <div class="abs" style="left:296px;top:150px">
    <h4>INFORMATION</h4>
    <ul><li>Privacy Policy</li><li>Your Account</li><li>Advanced Search</li><li>Contact Us</li></ul>
  </div>
  <div class="abs" style="left:536px;top:150px;width:240px">
    <h4>CONTACT US</h4>
    <div class="row"><svg width="12" height="16" viewBox="0 0 12 16"><path d="M6 0a6 6 0 0 1 6 6c0 4-6 10-6 10S0 10 0 6a6 6 0 0 1 6-6z" fill="#fff"/><circle cx="6" cy="6" r="2" fill="#0f0f0f"/></svg><span>218 Fernhill Row,<br>Brookvale, FL 30000</span></div>
    <div class="row"><svg width="12" height="14" viewBox="0 0 12 14"><path d="M2 0h3l1 4-2 1a8 8 0 0 0 3 4l1-2 4 1v3c0 1-1 3-3 3C4 14 0 8 0 3c0-2 1-3 2-3z" fill="#fff"/></svg><span>0155 010 7734</span></div>
    <div class="row"><svg width="14" height="11" viewBox="0 0 14 11"><rect width="14" height="11" rx="1" fill="#fff"/><polyline points="0,1 7,6 14,1" fill="none" stroke="#0f0f0f" stroke-width="1.4"/></svg><span>hello@verdantvigor.test</span></div>
  </div>
  <div class="abs" style="left:870px;top:150px;width:240px">
    <h4>JOIN OUR MAILING LIST</h4>
    <p style="line-height:20px">Your about us information would<br>fit here nicely.</p>
    <div class="mail"><span>Email address</span><svg width="16" height="16" viewBox="0 0 16 16"><circle cx="8" cy="8" r="7" fill="none" stroke="#fff" stroke-width="1.5"/><polyline points="7,5 10,8 7,11" fill="none" stroke="#fff" stroke-width="1.5"/></svg></div>
  </div>
  <div class="abs copy">Copyright © 2019 &nbsp;All Rights Reserved</div>
</footer>

</body>
</html>
```